Alberta, Canada based Environmental Oilfield Consultant need a Business Card Design

We need a business card design for a year old company based in Edmonton, Alberta, Canada called Cindermoor Consulting Inc. We are environmental consultants primarily for oilfield based companies (pipeline cleanup, site consultations, environmental site training, and site evaluations).

We like the color blue or green, something very clean and crisp looking.
We don't really care if there is an otter on it but most of our work is land based and nothing really to do with oceans or larger bodies of water.

The name Cindermoor was the name of our fathers boat, and named our company that in his memory.

```html
<!DOCTYPE html>
<html lang="en">
<head>
<meta charset="utf-8">
<title>Cindermoor Consulting – Business Card</title>
<link rel="stylesheet" href="https://fonts.googleapis.com/css2?family=Exo+2:wght@400;500;700&display=swap">
<style>
  :root {
    --backdrop: #e6e8eb;
    --card-light: #ffffff;
    --card-shade: #e4e6e9;
    --brand-blue: #2f7fd6;
    --deep-blue: #1f5fc4;
    --swoosh-cyan: #7fcfe0;
    --ink: #2b2e33;
    --ink-soft: #4a4e55;
  }
  * { margin: 0; padding: 0; box-sizing: border-box; }
  html, body {
    width: 1200px; height: 899px; overflow: hidden;
    background: var(--backdrop);
    font-family: "Exo 2", sans-serif;
  }
  .business-card {
    position: absolute; left: 130px; top: 181px;
    width: 940px; height: 537px;
    border-radius: 44px; overflow: hidden;
    background: radial-gradient(ellipse at 55% 40%, var(--card-light) 0%, var(--card-light) 45%, var(--card-shade) 100%);
    box-shadow: 0 18px 40px rgba(0,0,0,.18);
  }
  .card-swooshes { position: absolute; inset: 0; }
  .brand-name {
    position: absolute; left: 480px; top: 150px;
    color: var(--brand-blue);
    font-weight: 700; font-size: 64px; line-height: 66px;
    letter-spacing: 1px;
  }
  .contact-list {
    position: absolute; left: 42px; top: 244px;
    list-style: none; color: var(--ink-soft);
    font-size: 18px; line-height: 31px;
  }
  .contact-list li { display: flex; align-items: center; gap: 14px; }
  .contact-list svg { width: 18px; height: 18px; fill: var(--ink-soft); flex: none; }
  .contact-list .small { font-size: 16px; }
  .person { position: absolute; left: 560px; top: 330px; color: var(--ink); }
  .person-name { font-size: 26px; font-weight: 500; letter-spacing: 2px; }
  .person-role { font-size: 19px; padding-left: 64px; color: var(--ink-soft); }
  .office-address {
    position: absolute; left: 620px; top: 418px;
    font-size: 19px; line-height: 27px; color: var(--ink-soft);
    font-style: normal;
  }
</style>
</head>
<body>
  <article class="business-card">
    <svg class="card-swooshes" viewBox="0 0 940 537" aria-hidden="true">
      <defs>
        <linearGradient id="swoosh-blue" x1="0" y1="0" x2="1" y2="1">
          <stop offset="0" stop-color="#4fa8f0"/>
          <stop offset="1" stop-color="#1f5fc4"/>
        </linearGradient>
      </defs>
      <path d="M0 0 H250 C150 30 50 110 0 230 Z" fill="url(#swoosh-blue)"/>
      <path d="M320 0 C180 20 60 120 0 290" fill="none" stroke="var(--swoosh-cyan)" stroke-width="9"/>
      <path d="M940 537 H745 C850 520 925 440 940 320 Z" fill="url(#swoosh-blue)"/>
      <path d="M640 537 C800 530 915 440 940 290" fill="none" stroke="var(--swoosh-cyan)" stroke-width="9"/>
    </svg>

    <h1 class="brand-name">Cindermoor<br>Consulting</h1>

    <ul class="contact-list">
      <li><svg viewBox="0 0 24 24"><path d="M6.6 10.8a15 15 0 0 0 6.6 6.6l2.2-2.2c.3-.3.7-.4 1-.2 1.1.4 2.3.6 3.6.6.6 0 1 .4 1 1V20c0 .6-.4 1-1 1C10.6 21 3 13.4 3 4c0-.6.4-1 1-1h3.5c.6 0 1 .4 1 1 0 1.3.2 2.5.6 3.6.1.3 0 .7-.2 1z"/></svg>780 555 0142</li>
      <li><svg viewBox="0 0 24 24"><path d="M7 1h10a2 2 0 0 1 2 2v18a2 2 0 0 1-2 2H7a2 2 0 0 1-2-2V3a2 2 0 0 1 2-2zm0 3v14h10V4z"/></svg>780 555 0143</li>
      <li><svg viewBox="0 0 24 24"><path d="M6 2h9v5H6zM4 8h16a2 2 0 0 1 2 2v9H2v-9a2 2 0 0 1 2-2zm2 4v2h4v-2z"/></svg>780 555 0144</li>
      <li class="small"><svg viewBox="0 0 24 24"><path d="M2 5h20v14H2zm2 2v.5l8 5 8-5V7z"/></svg>info@cmoor.ca</li>
      <li class="small"><svg viewBox="0 0 24 24"><path d="M12 2a10 10 0 1 0 0 20 10 10 0 0 0 0-20zm0 2c1 1.3 1.8 3 2.1 5H9.9C10.2 7 11 5.3 12 4zM4.3 11h3.6a14 14 0 0 0 0 2H4.3a8 8 0 0 1 0-2zm5.6 0h4.2a12 12 0 0 1 0 2H9.9a12 12 0 0 1 0-2zm6.2 0h3.6a8 8 0 0 1 0 2h-3.6a14 14 0 0 0 0-2zM9.9 15h4.2c-.3 2-1.1 3.7-2.1 5-1-1.3-1.8-3-2.1-5z"/></svg>cindermoorinc.com</li>
    </ul>

    <div class="person">
      <p class="person-name">MARTIN HALE</p>
      <p class="person-role">Managing Director</p>
    </div>

    <address class="office-address">412,9th Floor,Crest<br>Jasper Avenue EDM</address>
  </article>
</body>
</html>
```